BrambleForge Development Studio Website

We'd like to create a brand new website for our company, so we can display our portfolio, our team, and our general approach to the app development work that we do. We've attached the website content + portfolio images for your convenience.

Our company is focused on substance over glamour, so we want our website to represent that mentality. We need something simple, and clean. We're open to both minimalist designs and as well as bolder designs.

Target Market(s)

Businesses: Startups and established companies

Coding

Coded - Design and coding required

Number of Pages Required

2 page

Font styles to use
Sans Serif

Colors
f78f20
faa54b
ffffff

Requirements
Must have
• We'd like this project to incorporate an orange highlight colour (#FFA300), but otherwise be more or less, black and white. If you'd like to also add a primary colour in your design (outside of the orange and grayscale colours), we're happy to explore it!

NOTICE: At the top of the portfolio section, we'd like a full banner highlighted section for Kelpwarden (a SaaS platform owned and operated by BrambleForge).
Nice to have
• We want the website design to be more on the clean side, for example, look at the portfolio section from: https://www.quillandmarsh.co.uk/ (ignore the top banner).

We're also open to exploring bold designs, something like: https://ferret.net/

```html
<!DOCTYPE html>
<html lang="en">
<head>
<meta charset="utf-8">
<title>Echo Pulse — BrambleForge</title>
<link href="https://fonts.googleapis.com/css2?family=Poppins:wght@400;500;600;700;800&display=swap" rel="stylesheet">
<style>
  :root{
    --orange:#ffa300;
    --orange-deep:#f29400;
    --pink:#ff346f;
    --ink:#444444;
    --text:#666666;
    --band:#f8f8f8;
    --footer:#4a4a4a;
    --footer-base:#3c3c3c;
    --white:#ffffff;
    --pill:#eeeeee;
  }
  *{margin:0;padding:0;box-sizing:border-box}
  html,body{width:1200px;height:2904px;overflow:hidden}
  body{position:relative;background:var(--white);font-family:"Poppins",sans-serif;color:var(--ink)}
  .abs{position:absolute}
  a{color:inherit;text-decoration:none}

  /* header */
  .brand{display:flex;align-items:center;gap:10px;font-weight:700;letter-spacing:.3px;white-space:nowrap}
  .brand-mark{width:20px;height:20px;background:var(--orange)}
  .site-brand{left:88px;top:22px;font-size:24px;color:var(--ink)}
  .main-nav{left:432px;top:26px;display:flex;gap:25px;font-size:15px;color:#555}

  /* hero */
  .hero-title{left:88px;top:240px;font-size:66px;line-height:62px;font-weight:800;color:var(--ink);width:640px;letter-spacing:.5px}
  .hero-title .accent{color:var(--pink)}
  .hero-sub{left:89px;top:455px;font-size:17px;color:#555}
  .tags{left:88px;top:500px;display:flex;gap:6px}
  .tag{background:var(--pill);border-radius:18px;height:34px;padding:0 16px;min-width:113px;display:flex;align-items:center;justify-content:center;font-size:12px;font-weight:600;letter-spacing:.4px;color:#555}
  .hero-circle{left:789px;top:214px;width:520px;height:520px;border-radius:50%;background:var(--pink)}
  .hero-art{left:722px;top:197px;width:406px;height:356px;border-radius:18px;background:linear-gradient(150deg,#6fb4e0,#2a78b8 60%,#1d5e9a)}

  /* band */
  .band{left:0;top:669px;width:1200px;height:502px;background:var(--band)}
  .section-title{font-size:34px;font-weight:800;color:var(--ink);letter-spacing:.4px}
  .copy{font-size:15.5px;line-height:26.7px;color:var(--text)}
  .bg-title{left:79px;top:905px}
  .bg-copy{left:468px;top:848px;width:580px}

  .brain-art{left:83px;top:1021px;width:443px;height:216px;background:linear-gradient(135deg,#e3e1fb,#c9c4f5 50%,#7fe0d0);border-radius:6px}

  .mock{left:77px;top:1237px;width:489px;height:308px;background:var(--white);border-radius:8px;box-shadow:0 30px 60px rgba(0,0,0,.12)}
  .mock-dots{position:absolute;left:27px;top:14px;display:flex;gap:6px}
  .mock-dots span{width:11px;height:11px;border-radius:50%}
  .mock-screen{position:absolute;left:9px;top:36px;width:471px;height:263px;background:#ececec;border-radius:4px;overflow:hidden}
  .mock-nav{position:absolute;left:22px;top:9px;display:flex;gap:20px;align-items:center;font-size:6px;font-weight:600;color:#333}
  .mock-nav .mock-brand{font-size:8px;font-weight:700;margin-right:10px}
  .mock-head{position:absolute;left:22px;top:95px;font-size:15px;line-height:20px;font-weight:800;color:#111;width:200px}
  .mock-text{position:absolute;left:22px;top:141px;font-size:5px;line-height:7px;color:#777;width:215px}
  .mock-btn{position:absolute;left:22px;top:164px;width:62px;height:16px;border-radius:8px;background:var(--pink);color:#fff;font-size:5px;font-weight:700;display:flex;align-items:center;justify-content:center}
  .mock-art{position:absolute;left:245px;top:70px;width:220px;height:130px;border-radius:6px;background:linear-gradient(135deg,#c7a6ff,#9d5de8 50%,#f6a04d)}

  .ch-title{left:652px;top:1293px}
  .ch-copy{left:652px;top:1346px;width:460px}

  .sol-title{left:87px;top:1793px}
  .sol-copy{left:87px;top:1846px;width:465px}
  .sol-circle{left:918px;top:1588px;width:370px;height:370px;border-radius:50%;background:var(--pink)}
  .sol-art{left:626px;top:1726px;width:485px;height:383px;border-radius:16px;background:linear-gradient(150deg,#cfe0fb,#8fb2ea 50%,#2c3470)}

  /* call to action */
  .cta{left:230px;top:2291px;width:736px;height:168px}
  .cta-title{left:255px;top:2376px;font-size:38px;font-weight:800;color:var(--white);letter-spacing:.5px;white-space:nowrap}
  .cta-rule{left:342px;top:2347px;width:204px;height:3px;background:var(--white)}
  .cta-icon{left:262px;top:2318px}
  .cta-btn{left:757px;top:2367px;width:168px;height:51px;border-radius:26px;background:var(--white);color:var(--ink);font-size:14px;font-weight:700;letter-spacing:.6px;display:flex;align-items:center;justify-content:center;box-shadow:0 6px 14px rgba(0,0,0,.12)}

  /* footer */
  .footer-shape{left:0;top:2440px}
  .foot-brand{left:127px;top:2632px;font-size:31px;color:var(--white);gap:12px}
  .foot-brand .brand-mark{width:26px;height:26px}
  .socials{left:201px;top:2689px;display:flex;gap:6px}
  .socials span{width:36px;height:36px;border-radius:50%;background:#5b5b5b;display:block}
  .foot-col{top:2570px;color:var(--white)}
  .foot-col h4{font-size:18px;font-weight:700;margin-bottom:16px;letter-spacing:.3px}
  .foot-col li{list-style:none;font-size:14px;line-height:28.5px}
  .col-links{left:501px}
  .col-work{left:690px}
  .col-contact{left:887px}
  .contact-item{display:flex;gap:10px;font-size:14px;line-height:18px;margin-bottom:20px}
  .contact-item svg{flex:none;margin-top:3px}
  .base-bar{left:0;top:2854px;width:1200px;height:50px;background:var(--footer-base);color:var(--white);font-size:12.5px;font-weight:500;display:flex;align-items:center;justify-content:center;letter-spacing:.2px}
  .to-top{left:1124px;top:2832px;width:40px;height:40px;border-radius:50%;background:var(--orange);display:flex;align-items:center;justify-content:center}
</style>
</head>
<body>

<header>
  <div class="abs brand site-brand"><span class="brand-mark"></span>BRAMBLEFORGE</div>
  <nav class="abs main-nav">
    <a>Portfolio</a><a>Our Approach</a><a>Who We Serve</a><a>Testimonials</a><a>Executive Team</a><a>Contact Us</a>
  </nav>
</header>

<section class="hero">
  <h1 class="abs hero-title"><span class="accent">Echo</span> Pulse<br>is a cutting<br>edge</h1>
  <p class="abs hero-sub">Neuroscientific music composition service</p>
  <div class="abs tags"><span class="tag">CONSULTING</span><span class="tag">STRATEGY</span></div>
  <div class="abs hero-circle"></div>
  <div class="abs hero-art" role="img" aria-label="Illustration of a person beside a large screen showing app content, with a plant and documents"></div>
</section>

<div class="abs band"></div>
<h2 class="abs section-title bg-title">Background</h2>
<p class="abs copy bg-copy">StackHarbor is a fast-growing startup company in the storage and logistics sector. They are going above &amp; beyond conventional warehousing &amp; storage lockers to provide a fully managed solution where business assets are catalogued, stored, and transported based on client needs with innovative technology deeply integrated into the process.</p>

<div class="abs brain-art" role="img" aria-label="Isometric illustration of a brain resting on a lotus with small figures around it"></div>

<div class="abs mock">
  <div class="mock-dots"><span style="background:#f44336"></span><span style="background:#ffb300"></span><span style="background:#4caf50"></span></div>
  <div class="mock-screen">
    <div class="mock-nav"><span class="mock-brand">ECHO PULSE</span><span>APPLICATION</span><span>OUR STORY</span><span>NEURO-MUSICAL SYNCHRONIZATION</span><span>SCIENCE</span></div>
    <div class="mock-head">THE NEW FRONTIER OF MUSIC AND THE BRAIN</div>
    <p class="mock-text">Blending neuroscience with sound, we shape music that can shift your mental state. Try it, learn more, and feel the change.</p>
    <div class="mock-btn">LEARN MORE</div>
    <div class="mock-art" role="img" aria-label="Illustration of a head with gears and people working on music"></div>
  </div>
</div>

<h2 class="abs section-title ch-title">Challenge</h2>
<p class="abs copy ch-copy">As StackHarbor was succeeding in the growth of their client base, managing the ever-growing inventory of items and the expanding use-cases from clients became a challenge with regards to operations and technology. Their existing technology and the corresponding processes started to become</p>

<h2 class="abs section-title sol-title">Solution</h2>
<p class="abs copy sol-copy">BrambleForge works with StackHarbor to understand their business, review their existing technology and learn about their current processes. By gaining a genuine understanding of the nuances of their business, BrambleForge provides on-going updates to restructure &amp; enhance the existing technologies. The main objective of these changes is to enhance operational efficiency and accuracy, and meet the ever-evolving requirements of new and existing StackHarbor clients.</p>
<div class="abs sol-circle"></div>
<div class="abs sol-art" role="img" aria-label="Isometric illustration of a large head with data layers and people working at laptops around it"></div>

<svg class="abs footer-shape" width="1200" height="420" viewBox="0 0 1200 420" aria-hidden="true">
  <polygon points="0,138 600,12 1200,138 1200,420 0,420" fill="var(--orange)"/>
  <polygon points="0,148 600,22 1200,148 1200,420 0,420" fill="var(--footer)"/>
</svg>

<section>
  <svg class="abs cta" viewBox="0 0 736 168" aria-hidden="true">
    <rect x="0" y="34" width="736" height="134" rx="14" fill="var(--orange-deep)"/>
    <path d="M14 0 H330 L444 150 Q452 168 430 168 H14 Q0 168 0 154 V14 Q0 0 14 0 Z" fill="var(--orange)"/>
  </svg>
  <svg class="abs cta-icon" width="60" height="56" viewBox="0 0 60 56" aria-hidden="true">
    <ellipse cx="22" cy="20" rx="20" ry="18" fill="#fff"/>
    <path d="M10 34 L6 46 L20 37 Z" fill="#fff"/>
    <path d="M40 16 A17 15 0 1 1 34 46 L40 52 L30 47" fill="none" stroke="#fff" stroke-width="4" stroke-linejoin="round"/>
  </svg>
  <div class="abs cta-rule"></div>
  <h2 class="abs cta-title">Have a project in mind?</h2>
  <a class="abs cta-btn">GET IN TOUCH</a>
</section>

<footer>
  <div class="abs brand foot-brand"><span class="brand-mark"></span>BRAMBLEFORGE</div>
  <div class="abs socials">
    <span aria-label="Social profile 1"></span><span aria-label="Social profile 2"></span><span aria-label="Social profile 3"></span><span aria-label="Social profile 4"></span>
  </div>

  <div class="abs foot-col col-links">
    <h4>Quick Links</h4>
    <ul><li>Portfolio</li><li>Our Approach</li><li>Who We Serve</li><li>Testimonials</li><li>Executive Team</li><li>Contact Us</li></ul>
  </div>
  <div class="abs foot-col col-work">
    <h4>Portfolio</h4>
    <ul><li>Kelpwarden</li><li>Quenly</li><li>StackHarbor</li><li>TileMarket</li><li>ChillSieve</li><li>EchoPulse</li></ul>
  </div>
  <div class="abs foot-col col-contact">
    <h4>Contact Us</h4>
    <div class="contact-item">
      <svg width="12" height="10" viewBox="0 0 12 10"><rect width="12" height="10" rx="1" fill="var(--orange)"/><path d="M0 1 L6 6 L12 1" stroke="var(--footer)" stroke-width="1.4" fill="none"/></svg>
      <span>Email:<br>www.example.com</span>
    </div>
    <div class="contact-item">
      <svg width="12" height="12" viewBox="0 0 12 12"><path d="M2 0 L4.5 0 L5 3 L3.5 4.2 Q4.8 7 7.8 8.5 L9 7 L12 7.5 L12 10 Q12 12 10 12 Q1 11 0 2 Q0 0 2 0 Z" fill="var(--orange)"/></svg>
      <span>Phone:<br>(818) 555-0142</span>
    </div>
    <div class="contact-item">
      <svg width="11" height="14" viewBox="0 0 11 14"><path d="M5.5 0 A5.5 5.5 0 0 1 11 5.5 C11 9 5.5 14 5.5 14 C5.5 14 0 9 0 5.5 A5.5 5.5 0 0 1 5.5 0 Z" fill="var(--orange)"/><circle cx="5.5" cy="5.5" r="2" fill="var(--footer)"/></svg>
      <span>Office Location:<br>Some address line goes<br>here with city...</span>
    </div>
  </div>

  <div class="abs base-bar">© COPYRIGHT BRAMBLEFORGE 2021. ALL RIGHTS RESERVED</div>
  <a class="abs to-top" aria-label="Back to top">
    <svg width="12" height="14" viewBox="0 0 12 14"><path d="M6 13 V2 M1.5 6 L6 1.5 L10.5 6" stroke="#fff" stroke-width="1.6" fill="none" stroke-linecap="round"/></svg>
  </a>
</footer>

</body>
</html>
```